Veltrano.co - Polar Expeditions Specialists

We need a modern, visually striking business card for Veltrano.co, a company specialized in selling expedition cruises to the most remote regions on Earth, with a focus on the Arctic and Antarctica. The design should instantly communicate that the cardholder is an expert in polar travel. Use clean, premium aesthetics with cool tones like icy blue and white, possibly incorporating polar imagery (ice, glaciers, penguins, etc.)

Attached the logo

Contact Information for Business Card

Feels high-end and trustworthy.. Visually memorable — encourages people to keep it

Colors
0054AA
0677BA
7BADD7
CADEEF
E8F1F8

Requirements
Must have
• ice, glaciers, penguins, montains
Nice to have
• modern, transparente,

```html
<!DOCTYPE html>
<html lang="en">
<head>
<meta charset="utf-8">
<title>Veltrano.co – Business Card</title>
<link href="https://fonts.googleapis.com/css2?family=Poppins:wght@500;700;800&family=Montserrat:wght@400;500&display=swap" rel="stylesheet">
<style>
  :root {
    --stage: #2b2b2d;
    --card-blue: #3777b6;
    --brand-blue: #3171b4;
    --deep-blue: #0054aa;
    --ice-light: #cadeef;
    --ice-pale: #e8f1f8;
    --white: #ffffff;
  }
  * { margin: 0; padding: 0; box-sizing: border-box; }
  html, body {
    width: 1200px; height: 875px; overflow: hidden;
    background: var(--stage);
  }
  .canvas {
    width: 1200px; height: 875px;
    display: flex; align-items: center; justify-content: center; gap: 60px;
  }
  .card {
    position: relative;
    width: 520px; height: 300px;
    border-radius: 22px;
    overflow: hidden;
    box-shadow: 0 18px 40px rgba(0,0,0,.45);
  }

  /* Back side */
  .card-back {
    background: var(--card-blue);
    display: flex; flex-direction: column; align-items: center; justify-content: center;
  }
  .card-back .brand-name {
    font-family: "Poppins", sans-serif; font-weight: 800;
    font-size: 64px; line-height: 1; letter-spacing: -1px;
    color: var(--deep-blue);
  }
  .card-back .brand-tagline {
    margin-top: 6px;
    font-family: "Poppins", sans-serif; font-weight: 700;
    font-size: 17px; color: var(--deep-blue);
  }
  .brand-row { display: flex; align-items: center; gap: 14px; }
  .brand-dot { width: 18px; height: 18px; border-radius: 50%; background: var(--deep-blue); }

  /* Front side */
  .card-front { background: var(--white); }
  .card-front .brand-block { position: absolute; left: 38px; top: 34px; }
  .card-front .brand-name {
    font-family: "Poppins", sans-serif; font-weight: 800;
    font-size: 62px; line-height: 1; letter-spacing: -1px;
    color: var(--brand-blue);
  }
  .card-front .brand-tagline {
    margin-top: 4px; padding-left: 22px;
    font-family: "Poppins", sans-serif; font-weight: 700;
    font-size: 18px; color: var(--brand-blue);
  }
  .card-front .brand-dot { background: var(--brand-blue); }

  .info-strip {
    position: absolute; left: 120px; right: 0; top: 168px; height: 54px;
    background: var(--brand-blue);
    display: flex; align-items: center; padding-left: 22px;
    color: var(--white);
  }
  .holder { padding-right: 16px; border-right: 1px solid var(--ice-pale); }
  .holder-name {
    font-family: "Poppins", sans-serif; font-weight: 700; font-size: 17px; line-height: 1.1;
  }
  .holder-title {
    font-family: "Montserrat", sans-serif; font-weight: 400; font-size: 11px;
  }
  .contact-list { list-style: none; padding-left: 14px; }
  .contact-list li {
    display: flex; align-items: center; gap: 6px;
    font-family: "Montserrat", sans-serif; font-weight: 500; font-size: 11px; line-height: 1.4;
  }
  .contact-list svg { width: 10px; height: 10px; fill: var(--white); }

  .base-band {
    position: absolute; left: 0; right: 0; bottom: 0; height: 48px;
    background: var(--brand-blue);
  }
</style>
</head>
<body>
<main class="canvas">
  <section class="card card-back" aria-label="Card back">
    <div class="brand-row">
      <span class="brand-dot"></span>
      <span class="brand-name">Veltrano.co</span>
    </div>
    <p class="brand-tagline">Polar Expeditions Specialists</p>
  </section>

  <section class="card card-front" aria-label="Card front">
    <div class="brand-block">
      <div class="brand-row">
        <span class="brand-dot"></span>
        <span class="brand-name">Veltrano.co</span>
      </div>
      <p class="brand-tagline">Polar Expeditions Specialists</p>
    </div>

    <div class="info-strip">
      <div class="holder">
        <p class="holder-name">Marco Lindqvist</p>
        <p class="holder-title">Managing Director</p>
      </div>
      <ul class="contact-list">
        <li>
          <svg viewBox="0 0 24 24" aria-hidden="true"><path d="M6.6 10.8a15 15 0 0 0 6.6 6.6l2.2-2.2c.3-.3.7-.4 1-.2 1.1.4 2.3.6 3.6.6.6 0 1 .4 1 1V20c0 .6-.4 1-1 1A17 17 0 0 1 3 4c0-.6.4-1 1-1h3.5c.6 0 1 .4 1 1 0 1.3.2 2.5.6 3.6.1.3 0 .7-.2 1z"/></svg>
          (555) 014-2283
        </li>
        <li>
          <svg viewBox="0 0 24 24" aria-hidden="true"><path d="M2 5h20v14H2z M2 5l10 8 10-8" /></svg>
          info@veltrano.co
        </li>
        <li>
          <svg viewBox="0 0 24 24" aria-hidden="true"><circle cx="12" cy="12" r="10"/></svg>
          www.veltrano.co
        </li>
      </ul>
    </div>

    <div class="base-band"></div>
  </section>
</main>
</body>
</html>
```